Bramblewood Card Company Business Cards

We are a trading card store with Glimmorax, sports and other TCG cards, we need a business card design that encompasses a clean cut, modern style with a retro flare. website is bramblewoodcardco.com for reference. Can utilize a comic book era feel or a more modern outdoor feel to utilize the "Pacific Northwest" elements of tress, mountains, etc.

Industry/Entity Type

Trading cards and collectibles

Contact Information for Business Card

business name, email address, phone number, name, owner job title

Font styles to use
Sans Serif

```html
<!DOCTYPE html>
<html lang="en">
<head>
<meta charset="utf-8">
<title>Bramblewood Card Company – Business Cards</title>
<link rel="stylesheet" href="https://fonts.googleapis.com/css2?family=Lato:wght@400;700;900&display=swap">
<style>
  :root {
    --backdrop: #2b2b2b;
    --card: #ffffff;
    --ink: #1f1f1f;
    --slate: #6f6f6f;
    --cyan: #0fb8dc;
    --rule: #2a2a2a;
  }
  * { box-sizing: border-box; margin: 0; padding: 0; }
  html, body {
    width: 1200px;
    height: 689px;
    overflow: hidden;
    background: var(--backdrop);
    font-family: "Lato", Arial, sans-serif;
  }
  .sheet {
    position: relative;
    width: 1200px;
    height: 689px;
  }
  .card {
    position: absolute;
    top: 190px;
    width: 540px;
    height: 309px;
    background: var(--card);
    border-radius: 26px;
    overflow: hidden;
  }
  .card--front { left: 40px; }
  .card--back  { left: 620px; }

  /* Front */
  .brand-front {
    position: absolute;
    inset: 0;
    display: flex;
    align-items: center;
    justify-content: center;
    gap: 16px;
  }
  .brand-front .brand-dot {
    width: 34px;
    height: 34px;
    border-radius: 50%;
    background: var(--cyan);
  }
  .brand-front .brand-name {
    font-weight: 900;
    font-size: 30px;
    line-height: 1.05;
    letter-spacing: 1px;
    text-transform: uppercase;
    color: var(--slate);
  }

  /* Back */
  .brand-back {
    position: absolute;
    top: 40px;
    right: 34px;
    text-align: right;
    font-weight: 900;
    font-size: 17px;
    line-height: 1.1;
    letter-spacing: 0.6px;
    text-transform: uppercase;
    color: var(--slate);
  }
  .divider {
    position: absolute;
    left: 34px;
    right: 34px;
    top: 196px;
    height: 1px;
    background: var(--rule);
  }
  .holder {
    position: absolute;
    left: 34px;
    top: 140px;
  }
  .holder-name {
    font-size: 25px;
    font-weight: 400;
    color: var(--cyan);
    letter-spacing: 0.2px;
    line-height: 1;
    text-transform: uppercase;
  }
  .holder-title {
    margin-top: 6px;
    font-size: 14px;
    color: var(--ink);
  }
  .contacts {
    position: absolute;
    left: 34px;
    top: 210px;
    list-style: none;
  }
  .contacts li {
    display: flex;
    align-items: center;
    gap: 10px;
    height: 22px;
    font-size: 14px;
    color: var(--ink);
  }
  .contacts svg {
    width: 14px;
    height: 14px;
    flex: none;
  }
  .icon-fill { fill: var(--slate); }
  .icon-line { fill: none; stroke: var(--slate); stroke-width: 2; stroke-linejoin: round; }
  .address {
    position: absolute;
    right: 34px;
    top: 212px;
    text-align: right;
    font-size: 14px;
    line-height: 1.5;
    color: var(--ink);
  }
</style>
</head>
<body>
<main class="sheet">

  <section class="card card--front" aria-label="Card front">
    <div class="brand-front">
      <span class="brand-dot"></span>
      <p class="brand-name">Bramblewood<br>Card Company</p>
    </div>
  </section>

  <section class="card card--back" aria-label="Card back">
    <p class="brand-back">Bramblewood<br>Card Company</p>

    <div class="holder">
      <p class="holder-name">Everett Lindqvist</p>
      <p class="holder-title">Managing Director</p>
    </div>

    <div class="divider"></div>

    <ul class="contacts">
      <li>
        <svg viewBox="0 0 24 24" aria-hidden="true"><path class="icon-fill" d="M6.6 10.8a15.1 15.1 0 0 0 6.6 6.6l2.2-2.2a1 1 0 0 1 1-.25 11.4 11.4 0 0 0 3.6.57 1 1 0 0 1 1 1V20a1 1 0 0 1-1 1A17 17 0 0 1 3 4a1 1 0 0 1 1-1h3.5a1 1 0 0 1 1 1c0 1.25.2 2.45.57 3.57a1 1 0 0 1-.25 1z"/></svg>
        044-318 672 905
      </li>
      <li>
        <svg viewBox="0 0 24 24" aria-hidden="true"><rect class="icon-line" x="3" y="6" width="18" height="12" rx="1"/><path class="icon-line" d="M3 7l9 6 9-6"/></svg>
        hello@cardmail.com
      </li>
      <li>
        <svg viewBox="0 0 24 24" aria-hidden="true"><circle class="icon-line" cx="12" cy="12" r="9"/><path class="icon-line" d="M3 12h18M12 3c-3 3.5-3 14.5 0 18M12 3c3 3.5 3 14.5 0 18"/></svg>
        www.bramblewoodcardco.com
      </li>
    </ul>

    <p class="address">218, Cedar Ridge Lane, Suite 4<br>98417, Evergreen Bay</p>
  </section>

</main>
</body>
</html>
```